Business Cards for new orthopaedic surgery practice

My husband and I are starting our own orthopaedic surgery practice. We are looking for a business card that is uniform, but one will have my name/title and the other will have his. You can just create one design with my name on it for now. But when I choose your design as the winning design I will ask that you add another copy with his name/title.

We are looking for classy, simple, elite all in one. We like dark blues/a little gold/yellow. Something that goes with our logo. We want our logo incorporated. Here is all the info you need:
Business name: RV Bone & Vitality Center
Location: 38517 North Willowmere Ave
Cedar Glen, FL 33990
Phone: 954-218-4063
Fax: 954-582-7341
Email: info@myrvbonecare.example

Names: Lydia Vance, M.D.
Board Certified Hand and Upper Extremity Surgeon

Ebo Dansu, M.D.
Board Certified Hip & Knee Replacement/General Orthopaedic Surgeon

Can decide what you want to put on the back. Maybe a slogan:
Rooted in Care. Focused on You

I am just going to upload our logo. The only thing is if we select you as the winning design, the location, and phone numbers may change. We will need your help to update that once fully solidified.

Industry/Entity Type

Medical

Contact Information for Business Card

Colors
0054AA
0677BA
7BADD7
CADEEF
E8F1F8
0094D4
00A9DD
6FCCEA
C7EBF8
E9F6FB

Requirements
Must have
• class, appeal,
Should not have
• We want to air on the side of masculine if we are looking at masculine vs. feminine feel. But we still want it classy, sophisticated, and something we will love

```html
<!DOCTYPE html>
<html lang="en">
<head>
<meta charset="utf-8">
<title>RV Bone &amp; Vitality Center – Business Card</title>
<link href="https://fonts.googleapis.com/css2?family=Fraunces:opsz,wght@9..144,600;9..144,800&family=Inter:wght@400;500&display=swap" rel="stylesheet">
<style>
  :root {
    --backdrop: #1c2b63;
    --card: #efe4d2;
    --ink: #1d2a66;
  }
  * { margin: 0; padding: 0; box-sizing: border-box; }
  html, body {
    width: 1200px; height: 800px; overflow: hidden;
    background: var(--backdrop);
  }
  .card {
    position: absolute;
    left: 328px;
    width: 530px; height: 302px;
    background: var(--card);
    color: var(--ink);
  }
  .card--front { top: 62px; }
  .card--back { top: 437px; }

  .doctor-name {
    position: absolute; left: 30px; top: 22px;
    font-family: "Fraunces", Georgia, serif;
    font-weight: 800;
    font-size: 58px; line-height: 52px;
    letter-spacing: -0.5px;
  }
  .credential {
    position: absolute; left: 31px; top: 134px;
    display: flex; align-items: center; gap: 6px;
    font-family: "Fraunces", Georgia, serif;
    font-weight: 800; font-size: 15px;
  }
  .credential::after {
    content: ""; width: 46px; height: 2px; background: var(--ink);
  }
  .practice-name {
    position: absolute; right: 30px; top: 40px;
    display: flex; align-items: center; gap: 9px;
    font-family: "Fraunces", Georgia, serif;
    font-weight: 600; font-size: 14px; line-height: 16px;
    text-transform: uppercase; letter-spacing: 0.3px;
  }
  .practice-name .mark {
    width: 30px; height: 30px; border-radius: 50%; background: var(--ink);
  }
  .specialty {
    position: absolute; left: 29px; top: 252px;
    font-family: "Inter", Arial, sans-serif;
    font-size: 16px;
  }
  .accent-dashes {
    position: absolute; left: 495px; top: 224px;
    display: flex; flex-direction: column; gap: 6px;
  }
  .accent-dashes span { width: 4px; height: 11px; background: var(--ink); }

  .contact-list {
    position: absolute; left: 29px; top: 66px;
    list-style: none;
    font-family: "Inter", Arial, sans-serif;
    font-size: 20px; line-height: 21px;
  }
  .contact-list li {
    display: flex; align-items: flex-start; gap: 19px;
    margin-bottom: 19px;
  }
  .contact-list li:first-child { margin-bottom: 22px; }
  .contact-list svg { width: 23px; height: 23px; flex: none; fill: var(--ink); }
  .practice-vertical {
    position: absolute; left: 481px; top: 32px;
    writing-mode: vertical-rl;
    font-family: "Inter", Arial, sans-serif;
    font-size: 20px;
  }
</style>
</head>
<body>
  <section class="card card--front">
    <h1 class="doctor-name">Lydia<br>Vance</h1>
    <p class="credential">M.D.</p>
    <div class="practice-name"><span class="mark"></span><span>RV Bone &amp;<br>Vitality<br>Center</span></div>
    <p class="specialty">Board Certified Hand and Upper Extremity Surgeon</p>
    <div class="accent-dashes"><span></span><span></span><span></span></div>
  </section>

  <section class="card card--back">
    <ul class="contact-list">
      <li>
        <svg viewBox="0 0 24 24" aria-hidden="true"><path d="M12 1a8 8 0 0 0-8 8c0 6 8 14 8 14s8-8 8-14a8 8 0 0 0-8-8zm0 11a3 3 0 1 1 0-6 3 3 0 0 1 0 6z"/></svg>
        <span>38517 North Willowmere Ave<br>Cedar Glen, FL 33990</span>
      </li>
      <li>
        <svg viewBox="0 0 24 24" aria-hidden="true"><path d="M6.6 10.8a15 15 0 0 0 6.6 6.6l2.2-2.2a1 1 0 0 1 1-.25 11.4 11.4 0 0 0 3.6.57 1 1 0 0 1 1 1V20a1 1 0 0 1-1 1A17 17 0 0 1 3 4a1 1 0 0 1 1-1h3.5a1 1 0 0 1 1 1c0 1.250.2 2.450.57 3.57a1 1 0 0 1-.25 1z"/></svg>
        <span>954-218-4063</span>
      </li>
      <li>
        <svg viewBox="0 0 24 24" aria-hidden="true"><path d="M2 8h4v14H2a1 1 0 0 1-1-1V9a1 1 0 0 1 1-1zm6-6h10l3 3v3h1a1 1 0 0 1 1 1v12a1 1 0 0 1-1 1H8zm2 2v4h9V5.5L17.5 4zm1 7v2h2v-2zm4 0v2h2v-2zm4 0v2h2v-2zm-8 4v2h2v-2zm4 0v2h2v-2zm4 0v2h2v-2z"/></svg>
        <span>954-582-7341</span>
      </li>
      <li>
        <svg viewBox="0 0 24 24" aria-hidden="true"><path d="M3 5h18a1 1 0 0 1 1 1v1l-10 6L2 7V6a1 1 0 0 1 1-1zm-1 4.3 10 6 10-6V18a1 1 0 0 1-1 1H3a1 1 0 0 1-1-1z"/></svg>
        <span>info@myrvbonecare.example</span>
      </li>
    </ul>
    <p class="practice-vertical">RV Bone &amp; Vitality Center</p>
  </section>
</body>
</html>
```